MRT Property - Business Cards

Looking for a business card & general letterhead, signage etc design for our new logo.

Colours:
000a20
0056a2
00b5ef
0088ce
68cef2

Fonts:
Poppins
Karla

Please keep look and feel of new brand - example in the zip package I sent.

```html
<!DOCTYPE html>
<html lang="en">
<head>
<meta charset="utf-8">
<title>MRT Property – Business Cards</title>
<link href="https://fonts.googleapis.com/css2?family=Poppins:wght@400;500;700;800&display=swap" rel="stylesheet">
<style>
  :root {
    --navy: #0c1222;
    --navy-soft: #161d30;
    --blue: #0056a2;
    --mid-blue: #0088ce;
    --cyan: #00b5ef;
    --light-blue: #68cef2;
    --white: #ffffff;
    --backdrop: #c4c4c6;
  }
  * { box-sizing: border-box; margin: 0; padding: 0; }
  html, body {
    width: 1200px; height: 900px; overflow: hidden;
    background: var(--backdrop);
    font-family: "Poppins", sans-serif;
  }
  .canvas { position: relative; width: 1200px; height: 900px; }
  .card {
    position: absolute;
    width: 680px; height: 388px;
    border-radius: 28px;
    background: var(--navy);
    overflow: hidden;
    box-shadow: 0 10px 24px rgba(0,0,0,0.28);
  }
  .card-back { left: 120px; top: 40px; }
  .card-front { left: 400px; top: 472px; }

  .back-mark {
    position: absolute; inset: 0;
    display: flex; align-items: center; justify-content: center;
    font-weight: 700; font-size: 58px; color: var(--navy-soft);
    letter-spacing: 1px;
  }

  .brand {
    position: absolute; left: 40px; top: 160px;
    font-weight: 700; font-size: 38px; color: var(--blue);
    line-height: 1; letter-spacing: 0.5px; white-space: nowrap;
  }
  .divider {
    position: absolute; left: 336px; top: 112px;
    width: 2px; height: 150px; background: var(--cyan);
  }
  .contact {
    position: absolute; left: 362px; top: 110px;
    color: var(--white);
  }
  .contact .name {
    font-weight: 800; font-size: 24px; color: var(--blue);
    text-transform: uppercase; line-height: 1.1; letter-spacing: 0.5px;
  }
  .contact .role { font-size: 15px; font-weight: 400; margin-top: 2px; }
  .contact .lines { list-style: none; margin-top: 20px; }
  .contact .lines li {
    display: flex; align-items: center; gap: 8px;
    font-size: 15px; line-height: 1.5; white-space: nowrap;
  }
  .contact .lines svg { width: 13px; height: 13px; flex: none; }

  .address-band {
    position: absolute; left: 0; right: 0; top: 306px; height: 28px;
    background: var(--cyan);
    display: flex; align-items: center;
    padding-left: 170px;
    color: var(--white); font-size: 15px; font-weight: 400;
    letter-spacing: 0.4px;
  }
</style>
</head>
<body>
<main class="canvas">
  <section class="card card-back" aria-label="Business card back">
    <div class="back-mark">MRT Property</div>
  </section>

  <section class="card card-front" aria-label="Business card front">
    <div class="brand">MRT Property</div>
    <div class="divider"></div>
    <div class="contact">
      <div class="name">Daniel Hayes</div>
      <div class="role">Managing Director</div>
      <ul class="lines">
        <li>
          <svg viewBox="0 0 24 24" aria-hidden="true"><path fill="#00b5ef" d="M6.6 10.8a15.1 15.1 0 0 0 6.6 6.6l2.2-2.2a1 1 0 0 1 1-.25 11.4 11.4 0 0 0 3.6.57 1 1 0 0 1 1 1V20a1 1 0 0 1-1 1A17 17 0 0 1 3 4a1 1 0 0 1 1-1h3.5a1 1 0 0 1 1 1c0 1.25.2 2.45.57 3.57a1 1 0 0 1-.25 1z"/></svg>
          123 456 789
        </li>
        <li>
          <svg viewBox="0 0 24 24" aria-hidden="true"><rect x="2" y="5" width="20" height="14" rx="2" fill="#00b5ef"/><path d="M3 6l9 7 9-7" fill="none" stroke="#0c1222" stroke-width="1.8"/></svg>
          info@example.com
        </li>
        <li>
          <svg viewBox="0 0 24 24" aria-hidden="true"><circle cx="12" cy="12" r="10" fill="#00b5ef"/><path d="M2 12h20M12 2c3 3 3 17 0 20M12 2c-3 3-3 17 0 20" fill="none" stroke="#0c1222" stroke-width="1.5"/></svg>
          www.example.com
        </li>
      </ul>
    </div>
    <div class="address-band">Your address, City State, Zip 1234</div>
  </section>
</main>
</body>
</html>
```